Flyer needed For the Council for Stewardship in Civic Ventures

With an increasing need for professional staffing in our design and construction industry it is important for organizations to be able to attract, support, and retain people of all genders. With the increase of women entering the design/construction industry, we need to be able to identify and address the specific needs of women in our industry, including those A/E’s who are on the facility Owner side.

This Forum will provide a venue to openly discuss the issues affecting our industry and ideas to address those issues.The program includes time for presentations and a panel discussion by accomplished women in our industry, and facilitated table and open discussions to form solutions with your peers. You will come away with ideas you can implement within your organization to build processes and a supportive culture for women

IN THE ATTACHMENTS
* you'll find our company logo

Target Market(s)

Women in the design and construction industry

Industry/Entity Type

Construction

Requirements
Must have
• Logo, event name, date, time, location, panelists names and pics, PBQ continuing education provided, contact information: Doreen Haskwell, doreen.haskwell@c-scvx.org, (512) 847-3096
• Register at: www.c-scvx.org/events
• Design should encompass the description given above.
Nice to have
• Colors that compliment our logo

```html
<!DOCTYPE html>
<html lang="en">
<head>
<meta charset="utf-8">
<title>AEC/O Industry Women's Mini-Forum &amp; Workshop</title>
<link rel="stylesheet" href="https://fonts.googleapis.com/css2?family=Mulish:wght@400;600;700;800&display=swap">
<style>
  :root {
    --blue: #4a5fa8;
    --blue-text: #3a57a4;
    --green: #8db243;
    --green-text: #a6c24a;
    --grey-dark: #555659;
    --grey-logo: #6d6e71;
    --white: #ffffff;
  }
  * { box-sizing: border-box; margin: 0; padding: 0; }
  html, body { width: 927px; height: 1200px; overflow: hidden; background: var(--white); }
  body { font-family: "Mulish", sans-serif; color: var(--grey-dark); }
  .flyer { position: relative; width: 927px; height: 1200px; overflow: hidden; }

  .brand { position: absolute; left: 52px; top: 40px; display: flex; align-items: center; gap: 16px; }
  .brand__dot { width: 92px; height: 92px; border-radius: 50%; background: var(--blue); }
  .brand__name { font-size: 44px; font-weight: 700; color: var(--grey-logo); letter-spacing: 1px; line-height: 1; }
  .brand__full { position: absolute; left: 176px; top: 101px; font-size: 11px; font-weight: 700; color: var(--green); }

  .hero-photo { position: absolute; left: 0; top: 140px; width: 927px; height: 385px;
    background: linear-gradient(100deg, #b8b2a6 0%, #d9d3c8 30%, #4a4644 48%, #8c8680 62%, #e6e1d8 85%, #cfc9bf 100%); }
  .hero-globe { position: absolute; left: 656px; top: 40px; width: 226px; height: 226px; border-radius: 50%;
    background: radial-gradient(circle at 40% 35%, #6f9ccf 0%, #2f5a93 55%, #0f2445 100%); }

  .tagline { position: absolute; left: 67px; top: 163px; color: var(--white); font-size: 18px; font-weight: 800; line-height: 21px; }
  .event-title { position: absolute; left: 68px; top: 368px; color: var(--white); font-weight: 800; line-height: 1; }
  .event-title__lead { font-size: 30px; }
  .event-title__big { font-size: 58px; letter-spacing: 0.5px; }
  .event-title__sub { display: block; font-size: 33px; margin-top: 2px; }
  .event-when { position: absolute; left: 68px; top: 471px; color: var(--green-text); font-size: 20px; font-weight: 700; line-height: 22px; }
  .event-when strong { display: block; font-weight: 800; font-size: 19px; }

  .intro { position: absolute; left: 67px; top: 527px; width: 800px; font-size: 15px; font-weight: 700; line-height: 20.2px; text-align: justify; }
  .formats { position: absolute; left: 110px; top: 773px; width: 760px; list-style: none; color: var(--blue-text); font-size: 13px; font-weight: 700; line-height: 16px; }
  .formats li { position: relative; padding-left: 17px; }
  .formats li::before { content: ""; position: absolute; left: 0; top: 4px; width: 7px; height: 7px; border-radius: 50%; background: var(--blue-text); }

  .mc-bar { position: absolute; left: 65px; top: 826px; width: 797px; height: 22px; background: var(--blue); color: var(--white); text-align: center; font-size: 15px; font-weight: 700; line-height: 22px; }
  .speaker { position: absolute; top: 860px; font-size: 13.5px; line-height: 17px; }
  .speaker__photo { width: 140px; height: 120px; border-radius: 8px; background: var(--green); margin-bottom: 8px; }
  .speaker__name { font-weight: 800; }
  .speaker--mc { left: 75px; }
  .speaker--keynote { left: 374px; }
  .speaker--moderator { left: 654px; }

  .panel { position: absolute; left: 76px; top: 1044px; list-style: none; font-size: 13.5px; line-height: 18.3px; }
  .panel__role { font-weight: 400; }
  .panel__names { color: var(--blue-text); font-weight: 700; }
  .ce-note { position: absolute; left: 560px; top: 1138px; color: var(--green); font-size: 13.5px; font-weight: 800; line-height: 18.3px; }

  .contact-bar { position: absolute; left: 0; top: 1163px; width: 927px; height: 37px; background: var(--blue); color: var(--white); display: flex; align-items: center; justify-content: center; gap: 10px; font-size: 15px; }
  .contact-bar svg { width: 12px; height: 12px; vertical-align: -1px; margin-right: 3px; }
  .contact-bar strong { font-weight: 800; margin-left: 4px; }
</style>
</head>
<body>
<main class="flyer">
  <div class="hero-photo" role="img" aria-label="Photograph of a confident businesswoman holding up a globe against a cloudy sky"></div>
  <div class="hero-globe" role="img" aria-label="Image of planet Earth held aloft"></div>

  <div class="brand">
    <span class="brand__dot"></span>
    <span class="brand__name">C-SCVx</span>
  </div>
  <p class="brand__full">Council for Stewardship in Civic Ventures</p>

  <p class="tagline">INVEST IN WOMEN<br>AND WATCH THEM THRIVE!</p>

  <h1 class="event-title">
    <span class="event-title__lead">AEC/O INDUSTRY </span><span class="event-title__big">WOMEN'S</span>
    <span class="event-title__sub">MINI-FORUM &amp; WORKSHOP</span>
  </h1>
  <p class="event-when">January 13, 2016 | 12:45 – 5:00 p.m. | Program 5:00 – 7:00 Reception
    <strong>LARKSPUR SUITES, CALDWELL SPRINGS, TEXAS</strong></p>

  <div class="intro">
    <p>With an increasing need for professional leadership and staffing in our design and construction industry it is important for organizations to be able to attract, support, and retain people of all genders. With the increase of women entering the design/construction industry, we need to be able to identify and address the specific needs of women in our industry, including those A/E's who are on the facility Owner side. This Forum will provide a venue to openly discuss the issues affecting our industry and ideas to address those issues.</p>
    <p>The program includes time for presentations and a panel discussion by accomplished women in our industry, and facilitated table and open discussions to form solutions with your peers. You will come away with ideas you can implement within your organization to build processes and a supportive culture for women.</p>
    <p>A visual note-taker will produce a comprehensive graphic in-the-moment, and a separate scribe will be utilized to compile the discussion ideas for distribution to the participants after the event.</p>
  </div>

  <ul class="formats">
    <li>Presenters and Panelists: architect, engineer, contractor, sub/trade, facility Owner</li>
    <li>Table Facilitators: one for each table, with tables divided into: architects, engineers, contractors, subs/trades, facility owners, educators</li>
  </ul>

  <h2 class="mc-bar">MASTER OF CEREMONIES</h2>

  <div class="speaker speaker--mc">
    <div class="speaker__photo"></div>
    <p class="speaker__name">MARION TERVASKEL,</p>
    <p>City Architect, City of Alder Ridge,<br>Founder and Chief Vision Officer, C-SCVx</p>
  </div>
  <div class="speaker speaker--keynote">
    <div class="speaker__photo"></div>
    <p>Keynote:</p>
    <p><span class="speaker__name">JUDGE LORNA VETTICK</span>,<br>Halvern County 150th District Court Pane</p>
  </div>
  <div class="speaker speaker--moderator">
    <div class="speaker__photo"></div>
    <p>Moderator –</p>
    <p><span class="speaker__name">PATRICE DUNMORE</span>,<br>President, Northgate Construction</p>
  </div>

  <ul class="panel">
    <li><span class="panel__role">ARCHITECTS: </span><span class="panel__names">Janine Holloway, Principal, Janine R. Holloway Architect</span></li>
    <li><span class="panel__role">ENGINEERS: </span><span class="panel__names">Tessa Gorvane, P.E., Brandt-Ellison; Mirela Quintana, Ostrand</span></li>
    <li><span class="panel__role">CONTRACTORS: </span><span class="panel__names">Colleen Bastaro, CEO, Bastaro Family Construction; Dana Pruett, Harlow Build</span></li>
    <li><span class="panel__role">OWNERS: </span><span class="panel__names">Odette Rennick, Sr. Project Manager, State University System-OFPC</span></li>
    <li><span class="panel__role">SUB/TRADES: </span><span class="panel__names">Gwen Farraday, CFO, RMX Mechanical</span></li>
    <li><span class="panel__role">EDUCATORS: </span><span class="panel__names">Aylin Dervan, Professor, CSU-South, (Civil Engineer)</span></li>
  </ul>
  <p class="ce-note">PBQ continuing education provided</p>

  <footer class="contact-bar">
    <span><svg viewBox="0 0 12 12" aria-hidden="true"><circle cx="6" cy="6" r="6" fill="#fff"/><path d="M3 4h6v4H3z M3 4l3 2.2L9 4" fill="none" stroke="#4a5fa8" stroke-width="0.9"/></svg>doreen.haskwell@c-scvx.org</span>
    <span><svg viewBox="0 0 12 12" aria-hidden="true"><circle cx="6" cy="6" r="6" fill="#fff"/><path d="M4 3.2c.6-.3 1 .9 1.1 1.4.1.4-.6.6-.4 1 .3.6.8 1.1 1.4 1.4.4.2.6-.5 1-.4.5.1 1.7.5 1.4 1.1-.4.9-1.4 1-2.2.6C5 7.6 4.3 6.9 3.7 5.7 3.3 4.9 3.3 3.6 4 3.2z" fill="#4a5fa8"/></svg>(512) 847-3096</span>
    <strong>Register at: www.c-scvx.org/events</strong>
  </footer>
</main>
</body>
</html>
```